Keystone Trench Co Business Card*

Looking for a professional, clean and crisp business card

I am in the underground utilities industry and am just looking for a really impressive business card. I would like our card to be white with our symbol crisp and clear with it protruding. I also have a business partner that will require his name and info on the card once the design is set. I would like to have our website info on the card which is;
http://keystonetrenchco.example/

Contact Information for Business Card

Website, contact name, number and email

```html
<!DOCTYPE html>
<html lang="en">
<head>
<meta charset="utf-8">
<title>Keystone Trench Co – Business Card</title>
<link href="https://fonts.googleapis.com/css2?family=Oswald:wght@600&family=Poppins:wght@400&display=swap" rel="stylesheet">
<style>
  :root {
    --page: #2a2a2a;
    --ink: #0b0b0b;
    --paper: #ffffff;
    --brand-blue: #3a5fb0;
    --back-dark: #0a0a0a;
    --back-mid: #1c1c1c;
  }
  * { margin: 0; padding: 0; box-sizing: border-box; }
  html, body { width: 1200px; height: 900px; overflow: hidden; background: var(--page); }
  .canvas { position: relative; width: 1200px; height: 900px; }

  .card { position: absolute; left: 250px; width: 700px; height: 400px; overflow: hidden; }

  /* back side */
  .card-back { top: 40px; background: var(--back-dark); }
  .back-texture {
    position: absolute; inset: 0;
    background: linear-gradient(135deg, var(--back-dark) 0%, var(--back-mid) 50%, var(--back-dark) 100%);
  }
  .back-mark {
    position: absolute; left: 50%; top: 50%; transform: translate(-50%, -50%);
    display: flex; align-items: center; gap: 16px; white-space: nowrap;
  }
  .mark-dot { width: 28px; height: 28px; border-radius: 50%; background: var(--paper); flex: none; }
  .back-mark .mark-name {
    font-family: 'Oswald', sans-serif; font-weight: 600; font-size: 40px;
    color: var(--paper); letter-spacing: 1px; text-transform: uppercase;
  }

  /* front side */
  .card-front { top: 460px; background: var(--paper); }
  .front-mark {
    position: absolute; left: 40px; top: 60px;
    display: flex; align-items: center; gap: 14px;
  }
  .front-mark .mark-dot { background: var(--ink); width: 26px; height: 26px; }
  .front-mark .mark-name {
    font-family: 'Oswald', sans-serif; font-weight: 600; font-size: 34px;
    color: var(--ink); text-transform: uppercase; line-height: 1.05; width: 190px;
  }

  .name-band {
    position: absolute; left: 0; top: 228px; width: 700px; height: 58px;
    background: var(--ink);
    display: flex; align-items: center; padding-left: 26px;
  }
  .name-band::after {
    content: ""; position: absolute; left: 300px; right: 24px; bottom: 10px;
    height: 2px; background: var(--paper);
  }
  .holder-name {
    font-family: 'Oswald', sans-serif; font-weight: 600; font-size: 30px;
    color: var(--paper); letter-spacing: 1.5px; text-transform: uppercase; line-height: 1;
  }

  .contact-list { position: absolute; left: 40px; top: 300px; list-style: none; }
  .contact-list li {
    display: flex; align-items: center; gap: 10px;
    font-family: 'Poppins', sans-serif; font-size: 18px; color: var(--ink); line-height: 29px;
  }
  .contact-list svg { width: 18px; height: 18px; flex: none; }
  .domain { color: var(--brand-blue); }
</style>
</head>
<body>
<main class="canvas">

  <section class="card card-back" aria-label="Card back">
    <div class="back-texture" role="img" aria-label="Dark diagonal pattern of pipe segments"></div>
    <div class="back-mark">
      <span class="mark-dot"></span>
      <span class="mark-name">Keystone Trench Co</span>
    </div>
  </section>

  <section class="card card-front" aria-label="Card front">
    <div class="front-mark">
      <span class="mark-dot"></span>
      <span class="mark-name">Keystone Trench Co</span>
    </div>

    <div class="name-band">
      <p class="holder-name">Dale Morrow</p>
    </div>

    <ul class="contact-list">
      <li>
        <svg viewBox="0 0 24 24" fill="none" stroke="var(--brand-blue)" stroke-width="2"><path d="M5 3h4l2 5-3 2a11 11 0 0 0 6 6l2-3 5 2v4a2 2 0 0 1-2 2A17 17 0 0 1 3 5a2 2 0 0 1 2-2z"/></svg>
        555-014-2238
      </li>
      <li>
        <svg viewBox="0 0 24 24" fill="none" stroke="var(--brand-blue)" stroke-width="2"><rect x="3" y="5" width="18" height="14"/><path d="M3 5l9 8 9-8"/></svg>
        dale@keystonetrenchco.example
      </li>
      <li>
        <svg viewBox="0 0 24 24" fill="none" stroke="var(--brand-blue)" stroke-width="2"><circle cx="12" cy="12" r="9"/><path d="M3 12h18M12 3a14 14 0 0 1 0 18M12 3a14 14 0 0 0 0 18"/></svg>
        <span>www.<span class="domain">keystonetrenchco</span>.example</span>
      </li>
    </ul>
  </section>

</main>
</body>
</html>
```